New Business Card Design for Manufacturing

We are an engineering/manufacturing company that offers Advanced machining/assembly/engineering services, as well as innovative products for the heavy duty engine cooling markets.

We are looking to get a new business card designed that is clean and modern looking, but still fits the wide range of technical/skilled work we do.

- We hope to use this design as the base for other design work in new Presentations, web, and print work.

Industry/Entity Type

Engineering

Contact Information for Business Card

Our preferred color of blue is (RGB) 22/71/159 but can vary slightly from that color. Our content will be our Logo and full company name (Vantrell Forge Works, Inc.), company address, name, job title, phone number with extension, cell number, fax number, website, and email address on the cards.
We'd like the full company name next to the logo, but we are open to other interpretations of that layout.
Preferably, we would like the back side to be clean with just our logo, and the front to contain all of the contact information.

Colors
2f74b4
0355a3
85abd2

Requirements
Must have
• - Logo, company name, needed content - We are open to interpretation beyond that.
• - Standard size business card.
• - Horizontal orientation.
• - Enough space for lengthy names / job titles (for example, a job title could read "Directory of Human Resources" or "V.P. of Governmental Affairs"). We need this to look clean, whether the title be short (CEO) or long (as described above).

```html
<!DOCTYPE html>
<html lang="en">
<head>
<meta charset="utf-8">
<title>Vantrell Forge Works – Business Card</title>
<link href="https://fonts.googleapis.com/css2?family=Montserrat:wght@600;700;800&family=Open+Sans:wght@400;600&display=swap" rel="stylesheet">
<style>
  :root {
    --stage: #1f1f21;
    --brand-blue: #16479f;
    --card-blue: #1451a6;
    --card-blue-deep: #0e3f8c;
    --paper: #ffffff;
    --ink: #4a4a4a;
    --rule: #8c8c8c;
    --band-grey: #9a9a9a;
    --link-blue: #0355a3;
  }
  * { box-sizing: border-box; margin: 0; padding: 0; }
  html, body {
    width: 1200px; height: 896px; overflow: hidden;
    background: var(--stage);
  }
  .stage { position: relative; width: 1200px; height: 896px; }

  .card {
    position: absolute;
    left: 353px;
    width: 487px; height: 277px;
    border-radius: 17px;
    overflow: hidden;
  }

  /* Back side */
  .card-back {
    top: 162px;
    background: var(--card-blue);
    display: flex; flex-direction: column; align-items: center; justify-content: center;
  }
  .card-back .brand-name {
    font-family: "Montserrat", sans-serif;
    font-weight: 800;
    font-size: 30px;
    line-height: 1.05;
    letter-spacing: 0.5px;
    color: var(--card-blue-deep);
    text-align: center;
    text-transform: uppercase;
  }
  .card-back .tagline {
    margin-top: 8px;
    font-family: "Montserrat", sans-serif;
    font-weight: 700;
    font-size: 13px;
    letter-spacing: 0.4px;
    color: var(--card-blue-deep);
    text-transform: uppercase;
  }

  /* Front side */
  .card-front {
    top: 469px;
    background: var(--paper);
  }
  .front-brand {
    position: absolute; left: 30px; top: 24px;
  }
  .front-brand .brand-name {
    font-family: "Montserrat", sans-serif;
    font-weight: 800;
    font-size: 27px;
    line-height: 1.02;
    color: var(--brand-blue);
    text-transform: uppercase;
  }
  .front-brand .tagline {
    margin-top: 6px;
    font-family: "Montserrat", sans-serif;
    font-weight: 700;
    font-size: 12.5px;
    color: #7d7d7d;
    text-transform: uppercase;
  }
  .person {
    position: absolute; right: 30px; top: 128px;
    text-align: right;
  }
  .person .name {
    font-family: "Montserrat", sans-serif;
    font-weight: 700;
    font-size: 18px;
    letter-spacing: 0.3px;
    color: var(--brand-blue);
    text-transform: uppercase;
  }
  .person .title {
    margin-top: 3px;
    font-family: "Open Sans", sans-serif;
    font-size: 11px;
    color: var(--ink);
  }
  .divider {
    position: absolute; left: 30px; right: 30px; top: 175px;
    height: 1px; background: var(--rule);
  }
  .contact-list, .address {
    position: absolute; top: 183px;
    list-style: none;
    font-family: "Open Sans", sans-serif;
    font-size: 11.5px;
    color: var(--ink);
  }
  .contact-list { left: 30px; }
  .contact-list li, .address li {
    height: 18px; display: flex; align-items: center; gap: 7px;
  }
  .contact-list svg { width: 10px; height: 10px; fill: var(--brand-blue); flex: none; }
  .address { right: 30px; text-align: right; }
  .address li { justify-content: flex-end; }
  .address .web { color: var(--link-blue); font-weight: 600; }

  .bottom-band {
    position: absolute; left: 0; bottom: 0; width: 487px; height: 6px;
  }
</style>
</head>
<body>
<main class="stage">

  <section class="card card-back" aria-label="Card back">
    <div class="brand-name">Vantrell<br>Forge Works</div>
    <div class="tagline">Built to Endure</div>
  </section>

  <section class="card card-front" aria-label="Card front">
    <div class="front-brand">
      <div class="brand-name">Vantrell<br>Forge Works, Inc.</div>
      <div class="tagline">Built to Endure</div>
    </div>

    <div class="person">
      <div class="name">Dana R. Whitfield</div>
      <div class="title">President</div>
    </div>

    <div class="divider"></div>

    <ul class="contact-list">
      <li>
        <svg viewBox="0 0 10 10" aria-hidden="true"><path d="M2 0.5 L3.6 2.6 L2.7 3.7 Q3.8 5.9 6.3 7.3 L7.4 6.4 L9.5 8 L8.2 9.5 Q4.5 9.3 2 6.5 Q0.3 4.3 0.5 1.8 Z"/></svg>
        +000.000.00 00
      </li>
      <li>
        <svg viewBox="0 0 10 10" aria-hidden="true"><path d="M2.5 0 H7.5 V10 H2.5 Z M3.4 1.2 V7.8 H6.6 V1.2 Z M4.5 8.4 H5.5 V9.3 H4.5 Z"/></svg>
        +000.000.00 00
      </li>
      <li>
        <svg viewBox="0 0 10 10" aria-hidden="true"><path d="M2.5 0 H7.5 V3 H2.5 Z M0.5 3.5 H9.5 V7.5 H8 V6 H2 V7.5 H0.5 Z M2.8 6.6 H7.2 V10 H2.8 Z"/></svg>
        +000.000.00 00
      </li>
      <li>
        <svg viewBox="0 0 10 10" aria-hidden="true"><path d="M0 2 H10 V8.5 H0 Z M0.6 2.4 L5 5.8 L9.4 2.4 V3.3 L5 6.7 L0.6 3.3 Z" fill-rule="evenodd"/></svg>
        www.yourmailaddress.com
      </li>
    </ul>

    <ul class="address">
      <li>Street Name Avenue, Suite 100</li>
      <li>State, Zip Code,Country</li>
      <li class="web">www.yourmailaddress.com</li>
    </ul>

    <svg class="bottom-band" viewBox="0 0 487 6" preserveAspectRatio="none" aria-hidden="true">
      <polygon points="0,0 243,0 237,6 0,6" fill="var(--brand-blue)"/>
      <polygon points="247,0 487,0 487,6 241,6" fill="var(--band-grey)"/>
    </svg>
  </section>

</main>
</body>
</html>
```